UX - Need some screens design for a Skill Assessment Application

I am building an app to carry out skill assessments. Depending on how the assessment is configured, it may have one or more parts
1. Question based assessment (Multiple Choice, True False, Fill in the blanks"
2. Endorsement by two colleagues - A screen that allows user to pick colleagues based on search and shows the status of pending requests
3. A written submission - a page that explains the format of the submission and a file upload
As each assessment can be configured with or without any of the steps, the assessment UI must be such that these areas get hidden/displayed based on configuration.
Colour codes to be used can be #0e78bb and #ffffff
There will also be a start screen (instructions) and an end screen (results)
Target Market(s)
Enterprise software
Number of Pages Required
4 page

```html
<!DOCTYPE html>
<html lang="en">
<head>
<meta charset="utf-8">
<link href="https://fonts.googleapis.com/css2?family=Inter:wght@400;500;600;700&display=swap" rel="stylesheet">
<style>
:root{
  --brand:#0e78bb;
  --nav:#0656ab;
  --white:#ffffff;
  --ink:#1d1f24;
  --muted:#5f6570;
  --faint:#a8adb5;
  --line:#dfe2e6;
  --band:#f4f5f7;
  --teal:#14999a;
  --chip:#e9eaec;
}
*{box-sizing:border-box;margin:0;padding:0}
html,body{width:1200px;height:771px;overflow:hidden;background:var(--white);font-family:"Inter",sans-serif;color:var(--ink)}
.app{position:relative;width:1200px;height:771px}
.topbar{position:absolute;left:0;top:0;width:1200px;height:43px;background:var(--nav)}
.brand{position:absolute;left:72px;top:11px;display:flex;align-items:center;gap:10px;color:var(--white);font-size:14px;font-weight:600}
.brand .dot{width:18px;height:18px;border-radius:50%;background:#55c3ee}
.mainnav{position:absolute;left:487px;top:0;display:flex;gap:21px;height:43px}
.mainnav a{color:#dce9f8;text-decoration:none;font-size:12.5px;line-height:46px;position:relative}
.mainnav a.active{color:var(--white);font-weight:700}
.mainnav a.active::after{content:"";position:absolute;left:0;right:0;bottom:0;height:2px;background:#2fb6e8}
.tools{position:absolute;right:72px;top:9px;display:flex;align-items:center;gap:16px}
.avatar-me{width:27px;height:27px;border-radius:50%;background:linear-gradient(135deg,#3a4b6b,#c7a48c)}
.crumbs{position:absolute;left:56px;top:65px;display:flex;align-items:center;gap:12px;font-size:11.5px;color:var(--muted)}
.crumbs a{color:var(--brand);text-decoration:none}
.title{position:absolute;left:88px;top:99px;display:flex;align-items:center;gap:14px}
.title h1{font-size:21.5px;font-weight:600}
.updated{position:absolute;right:90px;top:112px;font-size:11.5px;color:var(--muted)}
.updated b{font-weight:400;color:#3b4048}
.infoband{position:absolute;left:0;top:140px;width:1200px;height:45px;background:var(--band);border-top:1px solid var(--line);border-bottom:1px solid var(--line)}
.meta{position:absolute;left:88px;top:15px;display:flex;font-size:10.5px}
.meta span{padding:0 21px;border-left:1px solid #cfd3d8}
.meta span:first-child{padding-left:0;border-left:0}
.meta em{font-style:normal;color:var(--brand)}
.meta .plain{color:var(--muted)}
.chips{position:absolute;right:90px;top:10px;display:flex;gap:7px}
.chips span{background:var(--chip);border-radius:12px;padding:5px 9px;font-size:11.5px;color:#50555d}
.steps{position:absolute;left:88px;top:219px;width:214px}
.step{height:43px;border:1px solid var(--line);border-radius:4px;margin-bottom:8px;padding:0 17px;display:flex;align-items:center;justify-content:space-between;font-size:12.5px;color:#4a4f57}
.step.current{border-color:var(--brand);color:var(--ink);font-weight:500}
.step.locked{color:var(--faint)}
.panel{position:absolute;left:365px;top:213px;width:745px}
.panel h2{font-size:16px;font-weight:600;margin-top:7px}
.btn-outline{position:absolute;border:1px solid var(--brand);border-radius:3px;color:var(--brand);background:var(--white);font-size:11.5px;font-weight:500;display:flex;align-items:center;justify-content:center}
.btn-fill{position:absolute;background:var(--brand);border-radius:3px;color:var(--white);font-size:11.5px;font-weight:500;display:flex;align-items:center;justify-content:center}
.rule{position:absolute;left:0;top:41px;width:745px;height:1px;background:var(--line)}
.select,.search{position:absolute;top:59px;height:31px;border:1px solid var(--line);border-radius:3px;font-size:11.5px;display:flex;align-items:center;justify-content:space-between;padding:0 13px}
.search{color:var(--faint)}
.list{position:absolute;left:0;top:99px;width:745px}
.row{position:relative;height:58px;border:1px solid var(--line);border-radius:4px;margin-bottom:4.5px}
.check{position:absolute;left:13px;top:21px;width:14px;height:14px;border:1px solid #cfd3d8;border-radius:2px}
.check.on{background:var(--brand);border-color:var(--brand)}
.face{position:absolute;left:37px;top:14px;width:28px;height:28px;border-radius:50%}
.who{position:absolute;left:75px;top:14px}
.who .name{font-size:12px;font-weight:500}
.who .role{font-size:10.5px;color:var(--muted);margin-top:3px}
.row .btn-outline{right:13px;top:13px;width:49px;height:31px}
.pager{position:absolute;top:422px;right:0;display:flex;align-items:center}
.pg{width:62px;height:31px;border:1px solid var(--line);border-radius:3px;font-size:11px;color:#c4c8cd;display:flex;align-items:center;justify-content:center;gap:3px}
.num{width:33px;text-align:center;font-size:12.5px;color:#3b4048;margin-left:1.5px}
.num.on{background:var(--brand);color:var(--white);border-radius:3px;height:31px;line-height:31px}
.score{position:absolute;left:88px;top:663px;font-size:26px;font-weight:700}
.score small{font-size:13px;font-weight:500}
.progress{position:absolute;left:0;top:702px;width:1200px;height:7px;background:#f2f3f5}
.progress i{display:block;width:751px;height:7px;background:var(--teal)}
.skip{position:absolute;left:999px;top:731px;font-size:11.5px;color:#3b4048;display:flex;align-items:center;gap:4px}
</style>
</head>
<body>
<div class="app">
  <header class="topbar">
    <div class="brand"><span class="dot"></span>Assessly</div>
    <nav class="mainnav"><a class="active">Assessments</a><a>Colleagues</a><a>Results</a></nav>
    <div class="tools">
      <svg width="18" height="18" viewBox="0 0 24 24" fill="none" stroke="#fff" stroke-width="1.6"><path d="M6 16V11a6 6 0 0 1 12 0v5l2 2H4z"/><path d="M10 20a2 2 0 0 0 4 0"/></svg>
      <svg width="18" height="18" viewBox="0 0 24 24" fill="none" stroke="#fff" stroke-width="1.6"><circle cx="12" cy="12" r="3"/><path d="M12 2v3M12 19v3M2 12h3M19 12h3M4.9 4.9l2.1 2.1M17 17l2.1 2.1M4.9 19.1L7 17M17 7l2.1-2.1"/><circle cx="12" cy="12" r="7"/></svg>
      <div class="avatar-me" role="img" aria-label="User profile photo"></div>
    </div>
  </header>

  <div class="crumbs">
    <svg width="20" height="20" viewBox="0 0 24 24" fill="none" stroke="#0e78bb" stroke-width="1.8"><circle cx="12" cy="12" r="10"/><path d="M12 7l-5 5 5 5M7 12h10"/></svg>
    <a>Assessment</a><span>/</span><span>Application Design Capabilities</span>
  </div>

  <div class="title">
    <svg width="22" height="22" viewBox="0 0 24 24" fill="none" stroke="#5f6570" stroke-width="1.6"><path d="M14 21H5V3h12v8"/><path d="M8 7h6M8 11h6M8 15h3"/><circle cx="17" cy="17" r="3.5"/><path d="M15.5 17l1 1 2-2"/></svg>
    <h1>Application Design Capabilities</h1>
  </div>
  <div class="updated">Last Updated: <b>23/05/2024</b></div>

  <section class="infoband">
    <div class="meta">
      <span>Assessment Date: <em>May 20, 2024</em></span>
      <span>Assessment Type: <em>UI/UX Skill</em></span>
      <span>Due Date: <i class="plain" style="font-style:normal">24/05/2024</i></span>
    </div>
    <div class="chips"><span>Quiz</span><span>Endorsement</span><span>Submission</span></div>
  </section>

  <aside class="steps">
    <div class="step">Quiz
      <svg width="15" height="15" viewBox="0 0 16 16"><circle cx="8" cy="8" r="7" fill="#14999a"/><path d="M5 8.2l2 2 4-4" stroke="#fff" stroke-width="1.6" fill="none"/></svg>
    </div>
    <div class="step current">Endorsement</div>
    <div class="step locked">Submission</div>
  </aside>

  <main class="panel">
    <h2>Endorsement</h2>
    <div class="btn-outline" style="right:0;top:0;width:104px;height:31px">Save Progress</div>
    <div class="rule"></div>
    <div class="select" style="left:0;width:284px">All categories
      <svg width="12" height="12" viewBox="0 0 12 12"><path d="M2 4l4 4 4-4" stroke="#333" stroke-width="1.4" fill="none"/></svg>
    </div>
    <div class="search" style="left:291px;width:242px">Search
      <svg width="16" height="16" viewBox="0 0 24 24" fill="none" stroke="#666" stroke-width="2"><circle cx="11" cy="11" r="7"/><path d="M16 16l5 5"/></svg>
    </div>
    <div class="btn-fill" style="left:540px;top:59px;width:64px;height:31px">Search</div>
    <div class="btn-outline" style="right:0;top:59px;width:101px;height:31px">Send Request</div>

    <div class="list">
      <div class="row"><span class="check"></span><div class="face" role="img" aria-label="Colleague photo" style="background:linear-gradient(135deg,#5a3a26,#d9a57f)"></div><div class="who"><div class="name">Mei Lin Zhou</div><div class="role">Application Design Capabilities</div></div><div class="btn-outline">Add</div></div>
      <div class="row"><span class="check"></span><div class="face" role="img" aria-label="Colleague photo" style="background:linear-gradient(135deg,#2b2b2e,#8a7d73)"></div><div class="who"><div class="name">Harold Dunmore</div><div class="role">UI/UX Designer</div></div><div class="btn-outline">Add</div></div>
      <div class="row"><span class="check on"><svg width="14" height="14" viewBox="0 0 14 14"><path d="M3 7l3 3 5-6" stroke="#fff" stroke-width="1.8" fill="none"/></svg></span><div class="face" role="img" aria-label="Colleague photo" style="background:linear-gradient(135deg,#3d3530,#d6b9a3)"></div><div class="who"><div class="name">Mark Tennison</div><div class="role">Front-end Developer</div></div><div class="btn-outline">Add</div></div>
      <div class="row"><span class="check"></span><div class="face" role="img" aria-label="Colleague photo" style="background:linear-gradient(135deg,#e2a66a,#f3dcc8)"></div><div class="who"><div class="name">Alina Kovac</div><div class="role">Cybersecurity Analyst</div></div><div class="btn-outline">Add</div></div>
      <div class="row"><span class="check on"><svg width="14" height="14" viewBox="0 0 14 14"><path d="M3 7l3 3 5-6" stroke="#fff" stroke-width="1.8" fill="none"/></svg></span><div class="face" role="img" aria-label="Colleague photo" style="background:linear-gradient(135deg,#3a2c24,#cfc3b8)"></div><div class="who"><div class="name">Roland Clarke</div><div class="role">DevOps Engineer</div></div><div class="btn-outline">Add</div></div>
    </div>

    <div class="pager">
      <div class="pg">&#8249; Back</div>
      <span style="width:14px"></span>
      <div class="num on">1</div><div class="num">2</div><div class="num">3</div><div class="num">4</div><div class="num">5</div>
      <span style="width:15px"></span>
      <div class="pg">Next &#8250;</div>
    </div>
  </main>

  <div class="score">65<small>%</small></div>
  <div class="progress"><i></i></div>
  <div class="btn-outline" style="left:88px;top:723px;width:72px;height:31px">Go Back</div>
  <div class="skip">Skip <svg width="10" height="10" viewBox="0 0 10 10"><path d="M3 1l4 4-4 4" stroke="#333" stroke-width="1.4" fill="none"/></svg></div>
  <div class="btn-fill" style="left:1058px;top:723px;width:52px;height:31px">Next</div>
</div>
</body>
</html>
```